Valdo Capital

We need a corporate style website design for a new company based in Shenzhen's Qianhai Special Economic Development Zone, China. We provide a range of financial services to large international investment companies. Typically these companies invest over 5 million RMB. The company is part of a group that consists of NorthKilns, ValdoTrusts and ValdoEquity. Our location and gateway into Qianhai Special Economic Zone is our core advantage. We would like to see designs that Do Not use purple and orange. The website design should be similar to other websites in this family but different enough to give it a unique style (See attached website links for reference). The final design should communicate financial safety and growth. This website will act partly as a business chamber with connections to the government so we would like it to be diplomatic in style.

www.northkilns.example
www.valdotrusts.example

*Nevegation Bar
Should including Homepage, Financial Product, Team, News.
Could refer to www.valdotrusts.example

*Contact Details

Miss Lan
Address:E 728, North Block, KMO Centre, East Sector, Shenzhen Bright Science Campus
Telephone: +86 0755 63920417
Cellphone: +86 13957280316

* Social Media
Should be grouped like:
1. Weibo QRcode+ Weibo
2. Facebook, Twitter, Linkedin.

Industry/Entity Type

Investment

```html
<!DOCTYPE html>
<html lang="en">
<head>
<meta charset="utf-8">
<title>Valdo Capital</title>
<link rel="stylesheet" href="https://fonts.googleapis.com/css2?family=Open+Sans:wght@300;400;600&family=Raleway:wght@500;600&family=Ubuntu:wght@300;400;500&display=swap">
<style>
:root{
  --night-deep:#0b1a33;
  --night-mid:#1d3a63;
  --city-glow:#6a4a3a;
  --shade:rgba(8,10,16,.62);
  --white:#ffffff;
  --text-soft:#d7dde6;
  --nav-muted:#c9d0da;
  --panel:rgba(238,240,244,.93);
  --panel-text:#3a3d42;
  --accent:#8fd0ef;
  --accent-dark:#2e6f95;
  --social:#8b9096;
  --line:rgba(255,255,255,.45);
}
*{margin:0;padding:0;box-sizing:border-box}
html,body{width:1200px;height:984px;overflow:hidden}
body{position:relative;font-family:"Ubuntu",sans-serif;color:var(--white);background:var(--night-deep)}
.hero-photo{position:absolute;inset:0;background:
  radial-gradient(ellipse 500px 260px at 380px 600px,rgba(230,170,90,.45),transparent 70%),
  radial-gradient(ellipse 300px 500px at 660px 420px,rgba(200,210,230,.28),transparent 70%),
  linear-gradient(180deg,#1a2d52 0%,#2a4670 35%,#3d4a66 52%,var(--city-glow) 70%,#1b1d26 100%)}
.shade{position:absolute;inset:0}
.brand{position:absolute;left:110px;top:34px;display:flex;align-items:center;gap:14px;font-family:"Open Sans",sans-serif;font-weight:400;font-size:34px;letter-spacing:1px;color:var(--white)}
.brand-mark{width:34px;height:34px;border-radius:50%;background:var(--accent-dark)}
.lang{position:absolute;left:917px;top:22px;font-family:"Open Sans",sans-serif;font-size:13px;color:var(--nav-muted)}
.lang .current{text-decoration:underline;color:var(--white)}
.social{position:absolute;left:997px;top:19px;display:flex;gap:6px}
.social span{width:27px;height:27px;border-radius:50%;background:var(--social);border:2px solid rgba(255,255,255,.25)}
.main-nav{position:absolute;right:110px;top:65px;display:flex;gap:30px;font-family:"Open Sans",sans-serif;font-size:13px}
.main-nav a{color:var(--nav-muted);text-decoration:none}
.main-nav a.active{color:var(--white)}
.welcome{position:absolute;left:113px;top:236px;font-family:"Open Sans",sans-serif}
.welcome .pre{display:block;font-weight:300;font-size:58px;letter-spacing:-2px;color:#0d1526;line-height:66px}
.welcome h1{font-weight:600;font-size:61px;line-height:66px;letter-spacing:-1px}
.intro{position:absolute;left:119px;top:372px;width:460px;font-family:"Open Sans",sans-serif;font-size:17px;line-height:23px}
.read-more{color:var(--white);text-decoration:underline;font-size:16px}
.read-more::after{content:" ▸";font-size:11px;text-decoration:none;display:inline-block;margin-left:4px;color:var(--nav-muted)}
.about-card{position:absolute;left:110px;top:615px;width:223px;height:296px;background:var(--panel);border-radius:3px;padding:18px 12px;color:var(--panel-text)}
.about-card h2{font-family:"Raleway",sans-serif;font-weight:600;font-size:18px;margin-bottom:8px;color:#2c2f33}
.about-card p{font-size:12.5px;line-height:20px;font-weight:300;margin-bottom:12px}
.about-card .more{font-size:12.5px;color:#2c2f33;text-decoration:underline}
.about-card .more::after{content:" ▸";color:#888;text-decoration:none;display:inline-block;margin-left:4px}
.services{position:absolute;left:560px;top:646px;width:530px}
.services h2{font-family:"Raleway",sans-serif;font-weight:600;font-size:19px}
.services>p{font-size:12.5px;line-height:17px;margin-top:4px;padding-bottom:13px;border-bottom:1px dotted var(--line)}
.service{position:absolute;top:90px;width:230px}
.service svg{position:absolute;left:0;top:0}
.service h3{margin-left:60px;font-family:"Raleway",sans-serif;font-weight:600;font-size:19px}
.service p{margin-left:61px;font-size:12.5px;line-height:17px}
.service a{display:block;margin:6px 0 0 62px;color:var(--nav-muted);font-size:13px;text-decoration:none}
.arrow{position:absolute;top:745px}
.tabs{position:absolute;left:110px;top:874px;display:flex;gap:30px}
.tab{width:223px;height:37px;background:var(--white);border-radius:3px;display:flex;align-items:center;justify-content:space-between;padding:0 12px;font-family:"Raleway",sans-serif;font-weight:500;font-size:17px;color:#222}
.tab.first{font-size:19px;color:#333}
.footer{position:absolute;left:0;right:0;top:938px;border-top:1px dotted var(--line);font-size:13px;color:var(--nav-muted)}
.footer .copy{position:absolute;left:111px;top:13px}
.footer .legal{position:absolute;right:110px;top:13px}
</style>
</head>
<body>
<div class="hero-photo" role="img" aria-label="Night aerial view of a harbour city skyline with illuminated towers"></div>
<svg class="shade" width="1200" height="984" aria-hidden="true"><polygon points="1128,0 1200,0 1200,984 230,984" fill="var(--shade)"/></svg>

<header>
  <div class="brand"><span class="brand-mark"></span>Valdo Capital</div>
  <div class="lang"><span class="current">EN</span> &nbsp;|&nbsp; SP &nbsp;▾</div>
  <div class="social" aria-label="Social links"><span></span><span></span><span></span></div>
  <nav class="main-nav">
    <a class="active" href="#">HOME</a><a href="#">FINANCIAL PRODUCTS</a><a href="#">TEAM</a><a href="#">NEWS</a>
  </nav>
</header>

<section class="welcome">
  <span class="pre">Welcome To</span>
  <h1>Valdo Capital</h1>
</section>
<div class="intro">
  <p>Lorem ipsum dolor sit amet, consectetur adipisicing elit, sed do eiusmod tempor incididunt ut labore et dolore magna aliqua..</p>
  <p style="margin-top:6px"><a class="read-more" href="#">Read More</a></p>
</div>

<article class="about-card">
  <h2>About Us</h2>
  <p>Lorem ipsum dolor sit amet, consec-tetur adipisicing elit, sed do eius-mod tempor incididunt ut labore et dolore magna aliqua.</p>
  <p>Lorem ipsum dolor sit amet, consec-tetur adipisicing elit. labore et dolore magna aliqua..</p>
  <a class="more" href="#">Read More</a>
</article>

<section class="services">
  <h2>Our Services</h2>
  <p>Lorem ipsum dolor sit amet, consectetur adipisicing elit, sed do eiusmod tempor incididunt ut labore et dolore magna aliqua..</p>
  <div class="service" style="left:0">
    <svg width="50" height="56" viewBox="0 0 50 56"><rect x="8" y="4" width="30" height="18" rx="2" fill="#fff" transform="rotate(-12 23 13)"/><circle cx="23" cy="36" r="14" fill="#fff"/><rect x="0" y="30" width="12" height="20" rx="2" fill="#fff"/></svg>
    <h3>Finance</h3>
    <p>Valdo Capital lorem ipsum dolor sit amet..</p>
    <a href="#">Read More ⟶</a>
  </div>
  <div class="service" style="left:310px">
    <svg width="52" height="56" viewBox="0 0 52 56"><rect x="6" y="4" width="44" height="30" fill="none" stroke="#fff" stroke-width="4"/><polyline points="14,26 24,18 32,22 42,12" fill="none" stroke="#fff" stroke-width="3"/><line x1="28" y1="34" x2="18" y2="52" stroke="#fff" stroke-width="3"/><line x1="28" y1="34" x2="38" y2="52" stroke="#fff" stroke-width="3"/></svg>
    <h3>Consultancy</h3>
    <p>Valdo Capital lorem ipsum dolor sit amet..</p>
    <a href="#">Read More ⟶</a>
  </div>
</section>
<svg class="arrow" style="left:524px" width="22" height="42" aria-hidden="true"><polyline points="18,2 4,21 18,40" fill="none" stroke="rgba(255,255,255,.3)" stroke-width="5"/></svg>
<svg class="arrow" style="left:1106px" width="22" height="42" aria-hidden="true"><polyline points="4,2 18,21 4,40" fill="none" stroke="var(--accent-dark)" stroke-width="5"/></svg>

<nav class="tabs">
  <a class="tab first">About Us <svg width="14" height="24"><polyline points="3,2 12,12 3,22" fill="none" stroke="var(--accent)" stroke-width="3"/></svg></a>
  <a class="tab">What We Do <svg width="14" height="24"><polyline points="3,2 12,12 3,22" fill="none" stroke="#111" stroke-width="3"/></svg></a>
  <a class="tab">Our Blog <svg width="14" height="24"><polyline points="3,2 12,12 3,22" fill="none" stroke="#111" stroke-width="3"/></svg></a>
  <a class="tab">Who We Are <svg width="14" height="24"><polyline points="3,2 12,12 3,22" fill="none" stroke="#111" stroke-width="3"/></svg></a>
</nav>

<footer class="footer">
  <span class="copy">Copyright © 2014 Valdo Capital. All Rights Reserved</span>
  <span class="legal">Privacy Policy &amp; Term of Uses</span>
</footer>
</body>
</html>
```